Custom Seed Packet design for Flower Farm

We need a design for our seeds packets.
The design will be a kind of "fill in the blanks" as we need the design to be adaptable for multiple varieties of seed. We will be using the design for a rubber stamp.
Our seed packets are 90x90mm in size.
Black logo only. No colour required.
A vintage botanical influence is desired.
Will need to include the following info,
"Wrenfield Gable Co logo" , "Seeds", "Plant Type", "Variety", "Harvested"

```html
<!DOCTYPE html>
<html lang="en">
<head>
<meta charset="utf-8">
<title>Seed Packet Label – Wrenfield Gable Co Flower Farm</title>
<link href="https://fonts.googleapis.com/css2?family=Cinzel:wght@500&family=Barlow:wght@500;600&display=swap" rel="stylesheet">
<style>
  :root {
    --page: #ffffff;
    --paper-light: #ebcd92;
    --paper-mid: #ddb878;
    --paper-dark: #cfa563;
    --ink: #363636;
    --rule: #1f1f1f;
    --faint-bloom: rgba(150, 150, 140, 0.16);
  }
  html, body {
    margin: 0;
    width: 1200px;
    height: 1200px;
    overflow: hidden;
    background: var(--page);
  }
  .seed-label {
    position: absolute;
    left: 119px;
    top: 119px;
    width: 956px;
    height: 956px;
    background:
      radial-gradient(ellipse at 70% 80%, var(--paper-light) 0%, transparent 60%),
      linear-gradient(160deg, var(--paper-dark) 0%, var(--paper-mid) 45%, var(--paper-light) 100%);
  }
  .seed-label__frame {
    position: absolute;
    left: 35px;
    top: 35px;
    right: 35px;
    bottom: 35px;
    border: 5px solid var(--ink);
  }
  .botanical-backdrop {
    position: absolute;
    border-radius: 50% 50% 40% 40%;
    background: radial-gradient(ellipse at 50% 30%, var(--faint-bloom) 0%, transparent 70%);
  }
  .botanical-backdrop--right {
    left: 520px;
    top: 330px;
    width: 380px;
    height: 600px;
  }
  .botanical-backdrop--left {
    left: 55px;
    top: 670px;
    width: 210px;
    height: 250px;
  }
  .seed-label__title {
    position: absolute;
    left: 0;
    right: 0;
    top: 30px;
    margin: 0;
    text-align: center;
    font-family: "Cinzel", serif;
    font-weight: 500;
    font-size: 258px;
    letter-spacing: 6px;
    line-height: 1;
    color: var(--ink);
    transform: scaleY(1.22);
    transform-origin: top center;
  }
  .fill-field {
    position: absolute;
    left: 93px;
    width: 770px;
    height: 60px;
    border-bottom: 2px solid var(--rule);
  }
  .fill-field__label {
    position: absolute;
    left: 0;
    bottom: 10px;
    font-family: "Barlow", sans-serif;
    font-weight: 600;
    font-size: 20px;
    color: var(--ink);
  }
  .fill-field--plant-type { top: 431px; }
  .fill-field--variety    { top: 542px; }
  .fill-field--harvested  { top: 653px; }
  .farm-mark {
    position: absolute;
    left: 0;
    right: 0;
    top: 880px;
    text-align: center;
    font-family: "Barlow", sans-serif;
    font-weight: 500;
    font-size: 24px;
    line-height: 1.25;
    color: var(--ink);
  }
  .farm-mark__line { display: block; }
  .signature-line {
    position: absolute;
    left: 318px;
    width: 320px;
    top: 884px;
    border-top: 2px solid var(--rule);
  }
  .farm-mark-wrap {
    position: absolute;
    left: 0;
    right: 0;
    top: 0;
    height: 0;
  }
</style>
</head>
<body>
  <main class="seed-label">
    <div class="botanical-backdrop botanical-backdrop--right" role="img" aria-label="Faint line drawing of tall poppy stems and blooms"></div>
    <div class="botanical-backdrop botanical-backdrop--left" role="img" aria-label="Faint line drawing of two small poppies"></div>
    <div class="seed-label__frame"></div>

    <h1 class="seed-label__title">SEED</h1>

    <div class="fill-field fill-field--plant-type"><span class="fill-field__label">Plant Type</span></div>
    <div class="fill-field fill-field--variety"><span class="fill-field__label">Variety</span></div>
    <div class="fill-field fill-field--harvested"><span class="fill-field__label">Harvested</span></div>

    <div class="farm-mark" style="top:790px;">
      <span class="farm-mark__line">Wrenfield Gable Co.</span>
      <span class="farm-mark__line">Flower Farm</span>
    </div>

    <div class="signature-line"></div>
  </main>
</body>
</html>
```